Investment company needing business card

We are wanting a business card which looks sharp and easy on the eye. We are thinking of having a business card with the logo embossed on it, to really make it stand out. We will only have a small amount of information of the business card, person's name, position, email address and phone number

Contact Information for Business Card

Danielle Frost
Executive Assistant
+64 21 473 5162
danielf@harwickpartners.co.nz

Requirements
Must have
• Embossed logo
Should not have
• Not to be busy

```html
<!DOCTYPE html>
<html lang="en">
<head>
<meta charset="utf-8">
<title>Harwick Partners – Business Card</title>
<link href="https://fonts.googleapis.com/css2?family=Roboto:wght@400;500&family=Roboto+Condensed:wght@500;700&display=swap" rel="stylesheet">
<style>
  :root {
    --backdrop: #2a2a2a;
    --card: #f2f2f2;
    --brand-green: #20b873;
    --ink-grey: #5f5f5f;
    --text-dark: #4a4a4a;
    --rule: #bdbdbd;
  }
  * { margin: 0; padding: 0; box-sizing: border-box; }
  html, body {
    width: 1200px;
    height: 960px;
    overflow: hidden;
    background: var(--backdrop);
  }
  .business-card {
    position: absolute;
    left: 300px;
    top: 309px;
    width: 600px;
    height: 343px;
    background: var(--card);
    border-radius: 18px;
  }
  .brand {
    position: absolute;
    left: 110px;
    top: 89px;
    display: flex;
    align-items: center;
    gap: 14px;
  }
  .brand-mark {
    width: 60px;
    height: 60px;
    background: var(--ink-grey);
  }
  .brand-name {
    font-family: "Roboto Condensed", sans-serif;
    font-weight: 700;
    font-size: 36px;
    letter-spacing: 1px;
    color: var(--brand-green);
    text-transform: uppercase;
    line-height: 1;
  }
  .holder {
    position: absolute;
    right: 338px;
    top: 200px;
    text-align: right;
    font-family: "Roboto Condensed", sans-serif;
    text-transform: uppercase;
  }
  .holder-name {
    font-weight: 700;
    font-size: 21px;
    color: var(--brand-green);
    line-height: 24px;
  }
  .holder-role {
    font-weight: 500;
    font-size: 16px;
    letter-spacing: 0.3px;
    color: var(--ink-grey);
    line-height: 20px;
  }
  .divider {
    position: absolute;
    left: 276px;
    top: 194px;
    width: 1px;
    height: 55px;
    background: var(--rule);
  }
  .contact {
    position: absolute;
    left: 292px;
    top: 192px;
    list-style: none;
    font-family: "Roboto", sans-serif;
    font-size: 14.5px;
    line-height: 18.5px;
    color: var(--text-dark);
  }
</style>
</head>
<body>
  <main class="business-card">
    <div class="brand">
      <span class="brand-mark"></span>
      <span class="brand-name">Harwick Partners</span>
    </div>

    <div class="holder">
      <p class="holder-name">Danielle Frost</p>
      <p class="holder-role">Executive Assistant</p>
    </div>

    <span class="divider"></span>

    <ul class="contact">
      <li class="contact-phone">+64 21 473 5162</li>
      <li class="contact-email">danielf@harwickpartners.co.nz</li>
      <li class="contact-web">www.harwickpartners.co.nz</li>
    </ul>
  </main>
</body>
</html>
```